Website for new dental office

I am Dr. Colin Ashford and am building a new dental practice. I specialize in general dentistry. I am young and have a higher end dental practice incorporating very new technologies and would like my website to reflect that. As many dental patients are older, the website must be very easy to navigate. I would like patients to be able to request appointments, and will eventually add on patient information forms (the health history, etc, that you normally fill out in the practice) from my practice management software, so leave an area for that.

Industry/Entity Type

Building

```html
<!DOCTYPE html>
<html lang="en">
<head>
<meta charset="utf-8">
<title>Ashford Dental Clinic</title>
<link href="https://fonts.googleapis.com/css2?family=Open+Sans:ital,wght@0,400;0,600;0,700;1,400&display=swap" rel="stylesheet">
<style>
:root{
  --teal:#2bbcc6;
  --teal-dark:#1fa9b3;
  --teal-text:#27b3bd;
  --navy:#1f5d6b;
  --orange:#f28a1a;
  --orange-light:#f9a63a;
  --ink:#4a4a4a;
  --muted:#6f6f6f;
  --line:#d9dcdd;
}
*{box-sizing:border-box;margin:0;padding:0}
html,body{width:1200px;height:1144px;overflow:hidden}
body{position:relative;font-family:"Open Sans",Arial,sans-serif;color:var(--ink);
  background:radial-gradient(ellipse 700px 500px at 0 200px,#bfe3f0 0%,rgba(255,255,255,0) 70%),
             radial-gradient(ellipse 500px 300px at 1200px 40px,#bfe3f0 0%,rgba(255,255,255,0) 70%),#fff}
.abs{position:absolute}
.brand{left:184px;top:52px;font-size:32px;font-weight:600;color:var(--teal-text);letter-spacing:.2px}
.contact{right:184px;top:50px;text-align:right}
.contact .label{font-size:15px;color:var(--teal-text)}
.contact .phone{font-size:24px;color:var(--navy);line-height:1.1}
.nav{left:179px;top:110px;width:841px;height:45px;background:linear-gradient(#3cc7d0,var(--teal-dark));border-radius:4px 4px 0 0;display:flex}
.nav a{color:#fff;text-decoration:none;font-size:14.5px;font-weight:600;line-height:45px;text-align:center;white-space:nowrap;border-right:1px solid rgba(255,255,255,.3);flex:none}
.nav a:last-child{border-right:0}
.hero{left:180px;top:155px;width:840px;height:348px;background:#fff;border:1px solid var(--line);border-top:0;border-radius:0 0 4px 4px;overflow:hidden}
.hero-photo{position:absolute;left:300px;top:0;width:540px;height:348px;background:linear-gradient(90deg,#fff 0%,#e7f1f6 20%,#c9dde9 55%,#e9e3de 100%)}
.hero h1{position:absolute;left:47px;top:104px;font-size:38px;font-weight:700;color:var(--teal-text);letter-spacing:.3px;white-space:nowrap}
.hero h2{position:absolute;left:47px;top:150px;font-size:21px;font-weight:600;color:var(--orange);white-space:nowrap}
.hero p{position:absolute;left:47px;top:178px;width:320px;font-size:11.5px;line-height:18px;color:var(--muted)}
.dots{position:absolute;left:48px;top:222px;display:flex;gap:3px}
.dots i{width:11px;height:11px;border-radius:50%;background:#a9a9a9}
.dots i:first-child{background:var(--teal)}
.welcome{left:184px;top:543px;width:570px}
.welcome h3{font-size:25px;font-weight:400;color:#444;white-space:nowrap}
.welcome h3 span{color:var(--teal-text)}
.welcome .lead{margin-top:6px;font-size:12.8px;line-height:19.5px;color:var(--muted)}
.welcome .body{margin-top:12px;font-size:10.4px;line-height:19.5px;color:var(--muted)}
.feature{top:744px;width:176px}
.feature h4{font-size:19px;font-weight:400;color:var(--teal-text);margin-bottom:6px;white-space:nowrap}
.feature .thumb{width:176px;height:90px}
.feature h5{margin-top:9px;font-size:12px;font-weight:600;color:#555}
.feature p{margin-top:4px;font-size:10px;line-height:16.5px;color:var(--muted);text-align:justify}
.btn{display:inline-block;margin-top:12px;width:87px;height:25px;line-height:25px;text-align:center;font-size:10.5px;font-weight:600;color:#fff;background:linear-gradient(var(--orange-light),var(--orange));border-radius:3px}
.appt{left:783px;top:538px;width:236px;height:273px;border:1px solid var(--line);background:#fff}
.appt h3{height:44px;line-height:44px;padding-left:18px;background:linear-gradient(#3cc7d0,var(--teal-dark));color:#fff;font-size:18px;font-weight:400;white-space:nowrap}
.field{position:absolute;left:19px;width:196px;height:25px;border:1px solid #cfd3d4;background:#fff;font-size:10px;color:#777;line-height:23px;padding-left:10px;border-radius:2px;white-space:nowrap}
.submit{position:absolute;left:18px;top:219px;width:197px;height:32px;line-height:32px;text-align:center;color:#fff;font-size:12.5px;font-weight:600;background:linear-gradient(var(--orange-light),var(--orange));border-radius:3px}
.quote{left:782px;top:822px;width:237px;height:154px;border:1px solid var(--line);border-radius:3px;background:linear-gradient(#fff,#f3f4f4)}
.quote p{position:absolute;left:31px;top:15px;width:184px;font-size:10.5px;line-height:18.2px;font-style:italic;color:#666}
.quote .mark{position:absolute;font-size:26px;font-weight:700;color:#555;font-style:normal;line-height:1}
.quote .author{position:absolute;left:31px;top:116px;font-size:11px;color:#444}
.quote svg{position:absolute;right:29px;top:116px}
.footer{left:0;top:1033px;width:1200px;height:111px;background:linear-gradient(#eceeef 0,#fff 14px)}
.footer nav{position:absolute;left:183px;top:28px;font-size:13.5px;color:#444;white-space:nowrap}
.footer nav span{margin:0 7px;color:#666}
.footer small{position:absolute;left:183px;top:56px;font-size:10px;color:#666}
.social{position:absolute;left:941px;top:26px;display:flex;gap:8px}
.social i{width:19px;height:19px;border-radius:2px}
</style>
</head>
<body>
<div class="abs brand">Ashford Dental Clinic</div>
<div class="abs contact"><div class="label">Make Appointment</div><div class="phone">555-014-2290</div></div>

<nav class="abs nav">
  <a style="width:87px">Home</a><a style="width:96px">About Us</a><a style="width:150px">Treatment &amp; Care</a><a style="width:88px">Services</a><a style="width:134px">Success Stories</a><a style="width:93px">Practices</a><a style="width:89px">Support</a><a style="width:104px">Contact</a>
</nav>

<section class="abs hero">
  <div class="hero-photo" role="img" aria-label="Photo of a smiling dentist with a patient in the treatment chair"></div>
  <h1>DENTAL TREATMENT</h1>
  <h2>AND HIGHER END DENTAL PRACTICE</h2>
  <p>Pellentesque habitant morbi tristique senectus et netus et malesuada fames ac turpis egestas.</p>
  <div class="dots"><i></i><i></i><i></i><i></i></div>
</section>

<section class="abs welcome">
  <h3>Welcome to <span>Ashford Dental Clinic</span></h3>
  <p class="lead">Donec iaculis diam a nisi accumsan viverra Duis sed tellus et tortor vestibulum gravida Praesent elementum elit at tellus Curabitur metus ipsum luctus eu</p>
  <p class="body">Curabitur iaculis tempus eros Curabitur vel mi sit amet magna malesuada ultrices Ut nisi erat fermentum vel congue id euismod in elit Fusce ultricies orci ac feugiat suscipit leo massa sodales velit et scelerisque mi tortor at ipsum Proin orci odio commodo ac gravida non tristique vel tellus Pellentesque nibh libero ultricies eu sagittis non mollis sed justo Praesent metus ipsum pulvinar pulvinar porta id fringilla at est Phasellus felis dolor scelerisque</p>
</section>

<article class="abs feature" style="left:182px">
  <h4>Dental Practice</h4>
  <div class="thumb" role="img" aria-label="Photo of a dentist examining a young patient" style="background:linear-gradient(120deg,#7ccbe0,#c9e7ef 55%,#e8c7b4)"></div>
  <h5>Class aptent taciti</h5>
  <p>Donec scelerisque leo ac risus Praesent sit amet est In dictum dolor eu dictum porttitor enim</p>
  <span class="btn">READ MORE</span>
</article>
<article class="abs feature" style="left:374px">
  <h4>Services Provide</h4>
  <div class="thumb" role="img" aria-label="Photo of a masked dentist at work" style="background:linear-gradient(120deg,#9aa3a8,#d7dbdd 50%,#b5bcc0)"></div>
  <h5>Class aptent taciti</h5>
  <p>Donec scelerisque leo ac risus Praesent sit amet est In dictum dolor eu dictum porttitor enim</p>
  <span class="btn">READ MORE</span>
</article>
<article class="abs feature" style="left:565px">
  <h4>Our Technology</h4>
  <div class="thumb" role="img" aria-label="Photo of a modern dental treatment room with a teal chair" style="background:linear-gradient(120deg,#e4ebee,#f4f7f8 50%,#6fc3bf)"></div>
  <h5>Class aptent taciti</h5>
  <p>Donec scelerisque leo ac risus Praesent sit amet est In dictum dolor eu dictum porttitor enim</p>
  <span class="btn">READ MORE</span>
</article>

<aside class="abs appt">
  <h3>Request Appointment</h3>
  <div class="field" style="top:57px">Your name</div>
  <div class="field" style="top:89px">Phone no.</div>
  <div class="field" style="top:120px">Email address</div>
  <div class="field" style="top:152px;width:95px">Select Date</div>
  <div class="field" style="top:152px;left:119px;width:95px">Select Time</div>
  <div class="field" style="top:185px">Purpose to meet</div>
  <div class="submit">SUBMIT NOW</div>
</aside>

<aside class="abs quote">
  <span class="mark" style="left:12px;top:17px">&ldquo;</span>
  <p>Proin orci odio commodo ac gravida non tristique vel tellus Pellentesque nibh libero ultricies eu sagittis non mollis sed justo Praesent metus ipsum pulvinar pulvinar porta id frin <span class="mark" style="position:static;font-size:18px;vertical-align:-6px">&rdquo;</span></p>
  <span class="author">By Author Name</span>
  <svg width="22" height="16" viewBox="0 0 22 16" fill="none" stroke="#555" stroke-width="1.4"><path d="M7 2 1 8l6 6M15 2l6 6-6 6"/></svg>
</aside>

<footer class="abs footer">
  <nav>Home<span>|</span>About Us<span>|</span>Treatment &amp; Care<span>|</span>Services<span>|</span>Success Stories<span>|</span>Practices<span>|</span>Support<span>|</span>Contact</nav>
  <small>© 2014 Company Name.&nbsp; All right reserved.&nbsp; Term of Use</small>
  <div class="social" aria-label="Social links"><i style="background:#3b5998"></i><i style="background:#4cc2ef"></i><i style="background:#1b7bb6"></i></div>
</footer>
</body>
</html>
```